I am a general contractor in Portland, Or. I would like a clean and simple design layout, maybe using the "didot" font, blue and dark bronze in colors are preferred. On one side of the card, it would be nice to have a logo(attached photo) and business name(KTW Construction). I don't need my job title on the card, just some thing along the lines of "gordon pike, general contractor". Thanks much.

Target Market(s)

Adults from 30-55 years old. Middle to upper class.

Industry/Entity Type

Contractor

Contact Information for Business Card

KTW Construction
Gordon L. Pike
2843 NE 71st Ave.
Portland, Or. 97288
541.555.0187

Font styles to use
Other font styles liked:
• didot

Colors
3277b5
7f7f7f

Requirements
Should not have
• Too much going on.

```html
<!DOCTYPE html>
<html lang="en">
<head>
<meta charset="utf-8">
<title>KTW Construction – Business Card</title>
<link rel="stylesheet" href="https://fonts.googleapis.com/css2?family=Playfair+Display:wght@400;700&display=swap">
<style>
  :root {
    --page-bg: #e4e5e8;
    --card-top: #f7f7f8;
    --card-bottom: #e3e4e7;
    --navy: #2a3489;
    --royal: #3550a8;
    --sky: #1fa3e0;
    --ink: #2f3138;
    --icon: #3a4da0;
  }
  * { margin: 0; padding: 0; box-sizing: border-box; }
  html, body {
    width: 1200px;
    height: 900px;
    overflow: hidden;
    background: var(--page-bg);
  }
  .canvas {
    position: relative;
    width: 1200px;
    height: 900px;
    display: flex;
    align-items: center;
    justify-content: center;
  }
  .card {
    position: relative;
    width: 1000px;
    height: 572px;
    border-radius: 56px;
    overflow: hidden;
    background: linear-gradient(170deg, var(--card-top) 0%, #ffffff 35%, var(--card-bottom) 100%);
    box-shadow: 0 18px 40px rgba(0,0,0,0.18);
  }
  .card__swoosh {
    position: absolute;
    inset: 0;
    width: 100%;
    height: 100%;
  }
  .contact-list {
    position: absolute;
    left: 48px;
    top: 112px;
    list-style: none;
    font-family: "Playfair Display", serif;
    color: var(--ink);
  }
  .contact-list__item {
    display: flex;
    align-items: center;
    gap: 16px;
    height: 36px;
    font-size: 21px;
    letter-spacing: 0.5px;
  }
  .contact-list__item--cont { padding-left: 38px; }
  .contact-list__icon { width: 22px; height: 22px; flex: none; }
  .brand {
    position: absolute;
    left: 300px;
    top: 96px;
    display: flex;
    align-items: center;
    gap: 32px;
  }
  .brand__dot {
    width: 112px;
    height: 112px;
    border-radius: 50%;
    background: var(--royal);
    flex: none;
  }
  .brand__name {
    font-family: "Playfair Display", serif;
    font-weight: 700;
    color: var(--navy);
    font-size: 66px;
    line-height: 1;
  }
  .holder {
    position: absolute;
    right: 120px;
    top: 296px;
    text-align right;
    text-align: right;
    font-family: "Playfair Display", serif;
  }
  .holder__name {
    color: var(--royal);
    font-size: 29px;
    letter-spacing: 2px;
  }
  .holder__role {
    color: var(--ink);
    font-size: 18px;
    letter-spacing: 2px;
    margin-top: 2px;
  }
</style>
</head>
<body>
<main class="canvas">
  <section class="card" aria-label="KTW Construction business card, front">
    <svg class="card__swoosh" viewBox="0 0 1000 572" aria-hidden="true">
      <defs>
        <linearGradient id="bandFill" x1="0" y1="0" x2="1" y2="0">
          <stop offset="0" stop-color="#2a3489"/>
          <stop offset="1" stop-color="#3a55ad"/>
        </linearGradient>
        <linearGradient id="steelFill" x1="0" y1="0" x2="1" y2="0">
          <stop offset="0" stop-color="#3d4048"/>
          <stop offset="0.5" stop-color="#8a8d93"/>
          <stop offset="1" stop-color="#4a4d55"/>
        </linearGradient>
      </defs>
      <path d="M0 318 C220 400 560 460 1000 338" fill="none" stroke="url(#steelFill)" stroke-width="16"/>
      <path d="M0 334 C240 425 580 478 1000 352" fill="none" stroke="#1fa3e0" stroke-width="8"/>
      <path d="M0 350 C250 445 600 492 1000 366 L1000 572 L0 572 Z" fill="url(#bandFill)"/>
      <path d="M0 350 C250 445 600 492 1000 366" fill="none" stroke="#ffffff" stroke-opacity="0.7" stroke-width="3"/>
    </svg>

    <ul class="contact-list">
      <li class="contact-list__item">
        <svg class="contact-list__icon" viewBox="0 0 24 24" aria-hidden="true"><path fill="var(--icon)" d="M6.6 2.5l3 3.2-1.8 2.4a14 14 0 0 0 8.1 8.1l2.4-1.8 3.2 3-1.9 3.4C10.9 20.6 3.4 13.1 3.2 4.4z"/></svg>
        <span>541.555.0187</span>
      </li>
      <li class="contact-list__item">
        <svg class="contact-list__icon" viewBox="0 0 24 24" aria-hidden="true"><path fill="var(--icon)" d="M12 1.5a7.5 7.5 0 0 0-7.5 7.5c0 5.6 7.5 13.5 7.5 13.5s7.5-7.9 7.5-13.5A7.5 7.5 0 0 0 12 1.5z"/><circle cx="12" cy="9" r="2.8" fill="#fff"/></svg>
        <span>2843 NE 71st Ave.</span>
      </li>
      <li class="contact-list__item contact-list__item--cont">
        <span>Portland, Or. 97288</span>
      </li>
      <li class="contact-list__item">
        <svg class="contact-list__icon" viewBox="0 0 24 24" aria-hidden="true"><rect x="2" y="5" width="20" height="14" rx="1.5" fill="var(--icon)"/><path d="M2.5 6l9.5 7 9.5-7" fill="none" stroke="#fff" stroke-width="1.6"/></svg>
        <span>gordon@ktwbuild.com</span>
      </li>
      <li class="contact-list__item">
        <svg class="contact-list__icon" viewBox="0 0 24 24" aria-hidden="true"><circle cx="12" cy="12" r="10" fill="var(--icon)"/><g fill="none" stroke="#fff" stroke-width="1.3"><ellipse cx="12" cy="12" rx="4.5" ry="10"/><path d="M2 12h20M4 7h16M4 17h16"/></g></svg>
        <span>www.ktwbuild.com</span>
      </li>
    </ul>

    <div class="brand">
      <span class="brand__dot" aria-hidden="true"></span>
      <h1 class="brand__name">KTW<br>Construction</h1>
    </div>

    <div class="holder">
      <p class="holder__name">GORDON L. PIKE</p>
      <p class="holder__role">GENERAL CONTRACTOR</p>
    </div>
  </section>
</main>
</body>
</html>
```